VENTURE CAPITAL GROUP BUSINESS CARD DESIGN

Venture Capital Group based in SF looking for a bold business card design. No trendy colour explosion, 3D effects etc. Just "simple" optical effects. Works on your brain, keeps your eye focused and sticks to your mind.
Target Market(s)
Technology startups
Industry/Entity Type
Venture Capital
Contact Information for Business Card
DESMOND WHITLAKE
MANAGING PARTNER
187 FENWORTH ST SAN FRANCISCO, CA 94187
415.555.0142 O
415.555.0147 F
415.555.0193 C
desmond@veldtmoorcapital.ventures

```html
<!DOCTYPE html>
<html lang="en">
<head>
<meta charset="utf-8">
<title>Veldtmoor Capital Group – Business Card</title>
<link rel="stylesheet" href="https://fonts.googleapis.com/css2?family=Arimo:wght@400;700&display=swap">
<style>
  :root {
    --page-bg: #e9e8e4;
    --green-deep: #0f5a1f;
    --green-mid: #1e7a32;
    --green-light: #3f9a52;
    --white: #ffffff;
    --silver-light: #f4f4f4;
    --silver-dark: #9a9a9a;
    --ink: #3a3a3a;
  }
  * { box-sizing: border-box; margin: 0; padding: 0; }
  html, body { width: 1200px; height: 950px; overflow: hidden; }
  body {
    background: var(--page-bg);
    font-family: "Arimo", Arial, sans-serif;
    position: relative;
  }
  .card {
    position: absolute;
    left: 250px;
    width: 700px;
    height: 400px;
    border-radius: 6px;
    overflow: hidden;
    box-shadow: 0 8px 24px rgba(0,0,0,.18);
  }
  .card-back { top: 45px; background: linear-gradient(160deg, var(--white) 0%, var(--silver-light) 45%, #cfcfcf 100%); }
  .card-front { top: 505px; }
  .card-art { position: absolute; inset: 0; width: 100%; height: 100%; }

  .back-mark {
    position: absolute; inset: 0;
    display: flex; flex-direction: column; align-items: center; justify-content: center; gap: 22px;
  }
  .back-mark .dot {
    width: 90px; height: 90px; border-radius: 50%;
    background: var(--green-mid);
  }
  .wordmark {
    color: var(--green-mid);
    font-weight: 400;
    letter-spacing: .08em;
    text-transform: uppercase;
    white-space: nowrap;
  }
  .back-mark .wordmark { font-size: 34px; }

  .front-brand { position: absolute; left: 38px; top: 118px; font-size: 25px; }
  .contact {
    position: absolute; left: 38px; top: 170px;
    color: var(--ink); font-size: 17px; line-height: 22px;
    list-style: none;
  }
  .contact .address { margin-bottom: 4px; }
  .contact li { display: flex; align-items: center; gap: 10px; }
  .contact svg { width: 16px; height: 16px; fill: var(--green-mid); flex: none; }
  .holder {
    position: absolute; right: 42px; top: 66px; text-align: right; color: var(--white);
  }
  .holder .name { font-size: 22px; font-weight: 700; letter-spacing: .01em; }
  .holder .title { font-size: 18px; font-weight: 400; margin-top: 3px; }
</style>
</head>
<body>

<section class="card card-back" aria-label="Card back">
  <div class="back-mark">
    <span class="dot"></span>
    <span class="wordmark">Veldtmoor Capital Group</span>
  </div>
</section>

<section class="card card-front" aria-label="Card front">
  <svg class="card-art" viewBox="0 0 700 400" aria-hidden="true">
    <defs>
      <radialGradient id="greenField" cx="0.72" cy="0.55" r="0.6">
        <stop offset="0" stop-color="#4aa35c"/>
        <stop offset="0.55" stop-color="#1e7a32"/>
        <stop offset="1" stop-color="#0f5a1f"/>
      </radialGradient>
      <linearGradient id="silverArc" x1="0" y1="0" x2="1" y2="1">
        <stop offset="0" stop-color="#f2f2f2"/>
        <stop offset="0.6" stop-color="#b5b5b5"/>
        <stop offset="1" stop-color="#7d7d7d"/>
      </linearGradient>
    </defs>
    <rect width="700" height="400" fill="url(#greenField)"/>
    <ellipse cx="130" cy="275" rx="436" ry="258" fill="url(#silverArc)"/>
    <ellipse cx="122" cy="278" rx="424" ry="250" fill="#ffffff"/>
  </svg>

  <div class="wordmark front-brand">Veldtmoor Capital Group</div>

  <ul class="contact">
    <li class="address">187 Fenworth ST San Francisco<br>CA 94187</li>
    <li class="office">
      <svg viewBox="0 0 16 16"><path d="M3 2h3l1 3-2 1.2a8 8 0 0 0 4.8 4.8L11 9l3 1v3a1 1 0 0 1-1 1A12 12 0 0 1 2 3a1 1 0 0 1 1-1z"/></svg>
      415.555.0142
    </li>
    <li class="fax">
      <svg viewBox="0 0 16 16"><path d="M4 1h8v4H4zM2 6h12a1 1 0 0 1 1 1v5h-3v3H4v-3H1V7a1 1 0 0 1 1-1zm3 5v3h6v-3z"/></svg>
      415.555.0147
    </li>
    <li class="cell">
      <svg viewBox="0 0 16 16"><path d="M5 1h6a1 1 0 0 1 1 1v12a1 1 0 0 1-1 1H5a1 1 0 0 1-1-1V2a1 1 0 0 1 1-1zm0 2v9h6V3zm3 10a.8.8 0 1 0 0 .1z"/></svg>
      415.555.0193
    </li>
    <li class="email">
      <svg viewBox="0 0 16 16"><path d="M1 4h14v9H1zm1 1 6 4 6-4v-.2H2z"/></svg>
      desmond@veldtmoorcapital.ventures
    </li>
  </ul>

  <div class="holder">
    <div class="name">Desmond Whitlake</div>
    <div class="title">Managing Partner</div>
  </div>
</section>

</body>
</html>
```